Resident Guide for Senior Living Community

I need to create an informational magazine for residents that live in an Assisted Living community. This magazine is designed to educate the resident about the different service options and features that the community provides. I don't want to use any of the pictures in the Word Document - please use the uploaded picture instead. The final design should be both informational and elegant. The text in the word document is the actual text that needs to be used in the Resident Guide. Thanks!

Target Market(s)

Senior citizens and adult children (55 - 65 years old)

Industry/Entity Type

Assisted Living

Requirements
Must have
• Must be elegant - think Velmont Hargrove. Needs to have a lot of pictures and the logo must be used. The logo is the Plaque that says The Birch Lodge.
Nice to have
• The Word doucment is the old Resident Guide - we are looking for a refresh using the same content.
Should not have
• please do not use any pictures from the Word Document other than the Logo.

```html
<!DOCTYPE html>
<html lang="en">
<head>
<meta charset="utf-8">
<title>Resident Guide – Special Services</title>
<link href="https://fonts.googleapis.com/css2?family=Lato:wght@300;400;700;900&display=swap" rel="stylesheet">
<style>
  :root {
    --bg: #eeeeee;
    --paper: #ffffff;
    --gold: #a88c26;
    --gold-rule: #a8912e;
    --ink-label: #6b5608;
    --ink-body: #8f7b2c;
    --photo-warm-a: #f3ece3;
    --photo-warm-b: #d8cbbb;
  }
  * { box-sizing: border-box; margin: 0; padding: 0; }
  html, body {
    width: 1200px; height: 1000px; overflow: hidden;
    background: var(--bg);
    font-family: "Lato", Arial, sans-serif;
  }
  .spread {
    position: absolute; left: 184px; top: 164px;
    width: 849px; height: 601px;
    background: var(--paper);
    overflow: hidden;
  }
  .page { position: absolute; top: 0; height: 601px; width: 424px; }
  .page--left { left: 0; }
  .page--right { left: 424px; width: 425px; }
  .rule {
    position: absolute; height: 3px; background: var(--gold-rule);
  }
  .page--left .rule { left: 26px; top: 26px; width: 368px; }
  .page--right .rule { left: 29px; top: 26px; width: 367px; }
  .running-head {
    position: absolute; right: 28px; top: 16px;
    font-size: 6.5px; font-weight: 300; color: var(--ink-body);
  }
  .title {
    position: absolute; left: 27px; top: 44px;
    font-size: 18px; color: var(--gold); font-weight: 300; letter-spacing: 0.1px;
  }
  .title strong { font-weight: 900; }
  .service {
    position: absolute; font-size: 9.1px; line-height: 12.8px;
    font-weight: 300; color: var(--ink-body); text-align: justify;
  }
  .page--left .service { left: 27px; width: 369px; }
  .page--right .service { left: 28px; width: 369px; }
  .service b { font-weight: 900; color: var(--ink-label); }
  .photo { position: absolute; }
  .photo--salon {
    left: 27px; top: 424px; width: 369px; height: 177px;
    background: linear-gradient(160deg, var(--photo-warm-a) 0%, #ece2d6 55%, var(--photo-warm-b) 100%);
  }
  .photo--suite {
    left: 28px; top: 41px; width: 368px; height: 245px;
    background: linear-gradient(120deg, #5fa8a0 0%, #d9d0c3 35%, #ece6dc 60%, #b99a72 100%);
  }
</style>
</head>
<body>
  <div class="spread">
    <section class="page page--left">
      <div class="rule"></div>
      <h1 class="title"><strong>Special Services</strong> Available to Residents</h1>

      <p class="service" style="top:90px"><b>Medical Director -</b> Our Medical Director is available for consultation with residents and families and on call for emergencies.</p>

      <p class="service" style="top:128px"><b>Director of Health Services -</b> Facilitating the healthcare needs of our residents around the clock, our Director of Healthcare Services monitors the 24- hour close personal hands on care provided by our in-house CNA staff, as well as coordinates services with our Home Health agency, BirchCare® in Your Home, hospice, physicians, pharmacies and durable medical equipment providers. She and her team also perform frequent checks of all vital signs to assure residents maintain an optimal level of health.</p>

      <p class="service" style="top:217px"><b>Podiatrist -</b> Our podiatrist visits regularly. Treatments may be covered by Medicare if criteria are met. Consent form required. Co-pay usually applies.</p>

      <p class="service" style="top:256px"><b>Hair Stylist -</b> The Birch Lodge Ladies and Gentlemen visit our excellent beautician/ barber, Della Whitcomb (30 years at The Birch Lodge) in our salon. By appointment each week. Charge to resident: $30 shampoo, cut and set; $80 perm; $80 color, men’s haircut $20.</p>

      <p class="service" style="top:320px"><b>Manicures, Pedicures -</b> Also provided are manicures by Opal. The charge for a manicure is $20; pedicure $28. These services are available by appointment weekly.</p>

      <p class="service" style="top:358px"><b>Flowers -</b> For that added touch; we will deliver fresh flowers to a resident’s suite or penthouse apartment or to your family member’s apartment/suite on a weekly basis or for special occasions. Prices generally range from $75 to $100 per arrangement, as you advise.</p>

      <div class="photo photo--salon" role="img" aria-label="Photo of a smiling resident in a sun hat seated in the salon chair"></div>
    </section>

    <section class="page page--right">
      <div class="running-head">Special Services Available to Residents</div>
      <div class="rule"></div>
      <div class="photo photo--suite" role="img" aria-label="Photo of a bright resident suite living room with teal cabinet, sofa and artwork"></div>

      <p class="service" style="top:301px"><b>Cable Television -</b> The buildings are pre-wired for cable television. Direct billing to resident by Cable Company. No charge for wireless internet.</p>

      <p class="service" style="top:340px"><b>Telephone -</b> All Suites and Penthouse apartments are pre-wired for telephone service. Direct billing to resident by our provider for a private phone number.</p>

      <p class="service" style="top:378px"><b>Laundry -</b> We provide twice weekly or more frequently as needed laundry service (including hand ironing) at no extra charge.</p>

      <p class="service" style="top:416px"><b>Transportation -</b> There is no charge for scheduled group trips, arranged through a variety of Limousine companies. For individual trips a charge will be made to the resident by a transportation company or CityLink. For wheelchair transportation, we have Ardent Transit. We have used this company on numerous occasions and are confident in recommending them to our residents’ families.</p>

      <p class="service" style="top:493px"><b>Bottled Water Soft Drinks/Fresh Juices -</b> We provide bottled mineral water, etc. upon request to all Suites and Penthouses.</p>

      <p class="service" style="top:532px"><b>Meals -</b> You are invited to dine with us for any meal. Please make your reservations at least 24 hours in advance. Charges for meals are $8 for breakfast, $12 for lunch and $10 for dinner. You may pay cash or direct us to use your petty cash account.</p>
    </section>
  </div>
</body>
</html>
```